Redesign of business card for Cedar Ridge Mechanical

We are looking for a new design for our business cards for Cedar Ridge Mechanical. We are a plumbing & HVAC construction company, operating on the West Coast of Canada and USA. Logo attached.
Industry/Entity Type
Construction - Plumbing & HVAC
Contact Information for Business Card
Name, address, phone numbers, email, website address
Look and feel
Each slider illustrates characteristics of the customer's brand and the style your logo design should communicate.

```html
<!DOCTYPE html>
<html lang="en">
<head>
<meta charset="utf-8">
<title>Cedar Ridge Mechanical – Business Card</title>
<link href="https://fonts.googleapis.com/css2?family=Poppins:wght@400;500;600;700&display=swap" rel="stylesheet">
<style>
  :root {
    --page-bg: #e8e3db;
    --card-bg: #cdc2b2;
    --ink: #141414;
    --ink-soft: #2a2a2a;
  }
  * { margin: 0; padding: 0; box-sizing: border-box; }
  html, body {
    width: 1200px;
    height: 1046px;
    overflow: hidden;
    background: var(--page-bg);
    font-family: "Poppins", sans-serif;
    color: var(--ink);
  }
  .business-card {
    position: absolute;
    left: 80px;
    top: 238px;
    width: 1040px;
    height: 571px;
    background: var(--card-bg);
    border-radius: 30px;
  }
  .card-frame {
    position: absolute;
    inset: 0;
  }
  .brand {
    position: absolute;
    left: 40px;
    top: 210px;
    width: 440px;
    display: flex;
    align-items: center;
    gap: 16px;
  }
  .brand-mark {
    width: 58px;
    height: 58px;
    flex: none;
    background: var(--ink);
  }
  .brand-name {
    font-weight: 600;
    font-size: 34px;
    line-height: 1.1;
    color: var(--ink);
  }
  .divider {
    position: absolute;
    left: 512px;
    top: 94px;
    width: 2px;
    height: 319px;
    background: var(--ink);
  }
  .person {
    position: absolute;
    left: 586px;
    top: 144px;
  }
  .person-name {
    font-size: 39px;
    line-height: 1.2;
    font-weight: 400;
  }
  .person-name .first { font-weight: 700; }
  .person-title {
    font-size: 21px;
    font-weight: 600;
    margin-top: 0;
    padding-left: 2px;
  }
  .contact-list {
    position: absolute;
    left: 596px;
    top: 282px;
    list-style: none;
  }
  .contact-item {
    display: flex;
    align-items: center;
    height: 33.5px;
    font-size: 22.5px;
    font-weight: 400;
  }
  .contact-icon {
    width: 20px;
    height: 20px;
    margin-right: 18px;
    flex: none;
  }
  .address {
    position: absolute;
    left: 0;
    right: 0;
    top: 474px;
    text-align: center;
    font-size: 21.5px;
    font-weight: 500;
    color: var(--ink-soft);
    padding-right: 0;
    transform: translateX(-0px);
  }
</style>
</head>
<body>
  <div class="business-card">
    <svg class="card-frame" width="1040" height="571" viewBox="0 0 1040 571" aria-hidden="true">
      <g fill="none" stroke="var(--ink)" stroke-width="11" stroke-linecap="butt">
        <!-- top run with two small breaks -->
        <path d="M 66 13 H 27 Q 13 13 13 27 V 544 Q 13 558 27 558 H 62"/>
        <path d="M 76 13 H 964"/>
        <path d="M 74 558 H 964"/>
        <path d="M 974 13 H 1013 Q 1027 13 1027 27 V 544 Q 1027 558 1013 558 H 974"/>
      </g>
    </svg>

    <div class="brand">
      <span class="brand-mark"></span>
      <span class="brand-name">Cedar Ridge Mechanical</span>
    </div>

    <div class="divider"></div>

    <div class="person">
      <p class="person-name"><span class="first">Marta</span> Kolarova</p>
      <p class="person-title">Founder &amp; CEO</p>
    </div>

    <ul class="contact-list">
      <li class="contact-item">
        <svg class="contact-icon" viewBox="0 0 24 24" aria-hidden="true">
          <path fill="var(--ink)" d="M6.6 10.8a15.1 15.1 0 0 0 6.6 6.6l2.2-2.2c.3-.3.7-.4 1-.2 1.1.4 2.3.6 3.6.6.6 0 1 .4 1 1V20c0 .6-.4 1-1 1A17 17 0 0 1 3 4c0-.6.4-1 1-1h3.5c.6 0 1 .4 1 1 0 1.3.2 2.5.6 3.6.1.3 0 .7-.2 1z"/>
        </svg>
        (555) 214-3870
      </li>
      <li class="contact-item">
        <svg class="contact-icon" viewBox="0 0 24 24" aria-hidden="true">
          <circle cx="12" cy="12" r="10" fill="var(--ink)"/>
          <path d="M2 12h20M12 2c3 3 3 17 0 20M12 2c-3 3-3 17 0 20" stroke="var(--card-bg)" stroke-width="1.4" fill="none"/>
        </svg>
        info@cedarridgemech.com
      </li>
      <li class="contact-item">
        <svg class="contact-icon" viewBox="0 0 24 24" aria-hidden="true">
          <rect x="2" y="6" width="20" height="14" fill="var(--ink)"/>
          <path d="M2 6l10 8 10-8" stroke="var(--card-bg)" stroke-width="1.6" fill="none"/>
        </svg>
        www.cedarridgemech.com
      </li>
    </ul>

    <p class="address">418 Alder Ln. Suite 120 Tacoma, WA 98402</p>
  </div>
</body>
</html>
```